Business Card Design - ChoiceCraft

Looking for creative, modern design, two sided for ChoiceCraft that is consistent with color and feel of website www.choicecraftpro.net.
Updates

Back of card will be used to promote products or have a quote revolving around decisions, change, leadership, innovation, creativity. Back should also have space to promote website, but optional to use the icon. Front of the card will need to use the icon and have standard place for name, job title, phone and email. We are not looking to put a mailing address or fax. Also want space to place a few words/phrase explaining what we do...such as individual growth and organizational development or tools, training, information...in addition, want the facebook icon small on the front somewhere as we are also on facebook.

Vector file uploaded of icon.

Target Market(s)

Professional coaching for individual growth and organizational development

Industry/Entity Type

Business

Requirements
Must have
• Icon...see attached.

```html
<!DOCTYPE html>
<html lang="en">
<head>
<meta charset="utf-8">
<title>ChoiceCraft Business Card</title>
<link rel="stylesheet" href="https://fonts.googleapis.com/css2?family=Arimo:wght@400;700&display=swap">
<style>
  :root {
    --page: #e4e6e8;
    --card-white: #ffffff;
    --brand-blue: #1b75bb;
    --deep-blue: #1a5fa8;
    --sky-blue: #29abe2;
    --pale-blue: #8fd3f2;
    --ink: #111111;
    --text: #222222;
    --mark-silver: #c9d3dc;
  }
  * { margin: 0; padding: 0; box-sizing: border-box; }
  html, body { width: 1200px; height: 398px; overflow: hidden; }
  body {
    background: var(--page);
    font-family: "Arimo", Arial, sans-serif;
    position: relative;
  }
  .card {
    position: absolute;
    border-radius: 22px;
    overflow: hidden;
    box-shadow: 0 2px 6px rgba(0,0,0,0.25);
  }
  .card-front {
    left: 48px; top: 40px; width: 524px; height: 300px;
    background: var(--card-white);
  }
  .card-back {
    left: 614px; top: 40px; width: 520px; height: 296px;
    background: linear-gradient(100deg, var(--pale-blue) 0%, #5cc2ee 45%, var(--sky-blue) 100%);
  }
  .front-waves { position: absolute; left: 0; top: 0; width: 524px; height: 300px; }
  .brand-mark {
    position: absolute; left: 94px; top: 24px;
    width: 104px; height: 104px; border-radius: 50%;
    background: radial-gradient(circle at 40% 35%, #eef3f7, var(--mark-silver) 70%, #8fa3b5);
    border: 4px solid var(--brand-blue);
  }
  .brand-name {
    position: absolute; left: 79px; top: 158px;
    font-size: 20px; font-weight: 700; color: var(--ink); letter-spacing: 0.6px;
  }
  .contact-list {
    position: absolute; left: 78px; top: 193px;
    list-style: none; font-size: 14px; color: var(--text); line-height: 18.5px;
  }
  .contact-list li { display: flex; align-items: center; gap: 6px; }
  .contact-list svg { width: 10px; height: 10px; flex: none; }
  .social-square { width: 10px; height: 10px; background: var(--deep-blue); border-radius: 2px; flex: none; }
  .holder { position: absolute; right: 24px; top: 42px; text-align: right; }
  .holder-name { font-size: 20px; font-weight: 700; color: var(--brand-blue); }
  .holder-title { font-size: 15px; color: var(--brand-blue); margin-top: 3px; }
  .tagline {
    position: absolute; right: 14px; top: 254px; width: 200px;
    text-align: right; color: #fff; font-size: 12.5px; line-height: 13.5px;
  }
  .quote-list { position: absolute; left: 36px; top: 22px; list-style: none; color: #fff; }
  .quote { margin-bottom: 13px; }
  .quote-text { font-size: 13px; position: relative; }
  .quote-text::before {
    content: "\201C"; font-size: 22px; font-weight: 700;
    position: absolute; left: -15px; top: -7px;
  }
  .quote-text::after {
    content: "\201D"; font-size: 22px; font-weight: 700;
    position: relative; top: 7px; margin-left: 1px; line-height: 0;
  }
  .quote-author { font-size: 13px; font-weight: 700; margin-top: 3px; }
  .back-mark {
    position: absolute; left: 382px; top: 170px; width: 104px; height: 104px;
    border-radius: 50%;
    background: radial-gradient(circle at 40% 35%, #eef3f7, var(--mark-silver) 70%, #8fa3b5);
    border: 4px solid var(--brand-blue);
  }
</style>
</head>
<body>
  <section class="card card-front">
    <svg class="front-waves" viewBox="0 0 524 300" aria-hidden="true">
      <defs>
        <linearGradient id="light-band" x1="0" y1="0" x2="1" y2="0">
          <stop offset="0" stop-color="#cdeefb"/>
          <stop offset="1" stop-color="#29abe2"/>
        </linearGradient>
      </defs>
      <path d="M130,300 C280,298 420,250 524,185 L524,300 Z" fill="url(#light-band)"/>
      <path d="M-10,245 C60,297 140,313 230,303 C320,288 410,183 534,143" fill="none" stroke="#1a5fa8" stroke-width="9"/>
      <path d="M-10,232 C60,284 140,300 230,290 C320,275 410,170 534,130" fill="none" stroke="#111" stroke-width="8"/>
    </svg>

    <div class="brand-mark" aria-hidden="true"></div>
    <div class="brand-name">ChoiceCraft</div>

    <ul class="contact-list">
      <li>
        <svg viewBox="0 0 10 10"><path d="M2,1 L4,3 L3,4 C4,6 5,7 6,7 L7,6 L9,8 L7.5,9.5 C4,9 1,6 0.5,2.5 Z" fill="#222"/></svg>
        123-456-789
      </li>
      <li>
        <svg viewBox="0 0 10 10"><rect x="0.5" y="2" width="9" height="6.5" fill="#222"/><path d="M0.5,2 L5,6 L9.5,2" stroke="#fff" fill="none"/></svg>
        info@choicecraftpro.net
      </li>
      <li>
        <svg viewBox="0 0 10 10"><circle cx="5" cy="5" r="4.3" fill="none" stroke="#222"/><path d="M0.7,5 H9.3 M5,0.7 C2.5,3 2.5,7 5,9.3 C7.5,7 7.5,3 5,0.7" fill="none" stroke="#222" stroke-width="0.8"/></svg>
        www.choicecraftpro.net
      </li>
      <li><span class="social-square" aria-hidden="true"></span>/choicecraftpro</li>
    </ul>

    <div class="holder">
      <div class="holder-name">Your Name</div>
      <div class="holder-title">Title</div>
    </div>

    <p class="tagline">Supporting individual<br>growth and<br>organizational development.</p>
  </section>

  <section class="card card-back">
    <ul class="quote-list">
      <li class="quote">
        <div class="quote-text">Try not to become a man of success, but rather a man of value.</div>
        <div class="quote-author">- Marcus Hale</div>
      </li>
      <li class="quote">
        <div class="quote-text">The only constant is change.</div>
        <div class="quote-author">- Theron Vale</div>
      </li>
      <li class="quote">
        <div class="quote-text">We are what we repeatedly do. Excellence is not an act, it is a habit.</div>
        <div class="quote-author">- Elena Brisk</div>
      </li>
      <li class="quote">
        <div class="quote-text">Simplicity is the ultimate sophistication.</div>
        <div class="quote-author">- Paolo Renzi</div>
      </li>
      <li class="quote">
        <div class="quote-text">Life is not fair - get used to it.</div>
        <div class="quote-author">- Dana Wexley</div>
      </li>
    </ul>
    <div class="back-mark" aria-hidden="true"></div>
  </section>
</body>
</html>
```